A Gallery type Web design

We are developing a Wordpress based website for a client that does design construction projects. E.g. Pools, Lobbies, Toilets, etc. The website will mainly be to showcase their past projects and the collections they have.
No programming required, we just need the designs!
A sample of what the client is looking for:
http://velmorati.it/
Pages to include:
• Home – A nice slider design to showcase selected photos
• Main Category Template
• Sub Category Template
• About us
• Contact us
Example of their Main Categories and their Sub Categories:
Collections - Granite
- Marble
- Sculpture
Projects - Private
- Public
- Commercial
- Overseas
Installation - Vanity tops
- Hall areas
- Toilets
The Main Category is to show a sample and link the user to the respective Sub Categories. The Sub Categories are to showcase all the photos they have from the category. Please leave a little space to add some text or caption for the photo.
Designs need to be mobile responsive!
I've attached their logo and some sample photos to use for mock ups. Let me know if you have any questions!

```html
<!DOCTYPE html>
<html lang="en">
<head>
<meta charset="utf-8">
<title>Granvia Stone – Home</title>
<link href="https://fonts.googleapis.com/css2?family=Raleway:wght@400;500;600;700&display=swap" rel="stylesheet">
<style>
:root{
  --red:#d42a1e;
  --ink:#3f3f3f;
  --muted:#6e6e6e;
  --topbar:#f8f6f7;
  --header:#a6a6a6;
  --nav:#4a4a4a;
  --footer:#3a3a3a;
  --line:#e2e2e2;
  --white:#ffffff;
}
*{box-sizing:border-box;margin:0;padding:0}
html,body{width:811px;height:1200px;overflow:hidden;background:var(--white)}
body{position:relative;font-family:'Raleway',sans-serif;color:var(--ink)}
.abs{position:absolute}

.topbar{left:0;top:0;width:811px;height:33px;background:var(--topbar);border-bottom:1px solid #e4e4e4}
.contact-item{top:11px;font-size:8.5px;color:var(--muted);display:flex;align-items:center;gap:5px}
.contact-item svg{width:8px;height:8px;fill:#666}

.site-header{left:0;top:33px;width:811px;height:82px;background:var(--header)}
.brand{left:92px;top:22px;display:flex;align-items:center;gap:8px;font-size:18px;font-weight:700;color:var(--red);letter-spacing:.5px}
.brand-mark{width:14px;height:14px;background:var(--red)}
.follow{left:622px;top:22px;font-size:10px;color:var(--white)}
.socials{left:622px;top:40px;display:flex;gap:3px}
.socials span{width:22px;height:22px;border-radius:50%;display:block}

.main-nav{left:0;top:115px;width:811px;height:38px;background:var(--nav)}
.nav-link{top:13px;font-size:10.5px;color:var(--white)}

.hero{left:0;top:153px;width:811px;height:301px;background:linear-gradient(160deg,#2b2b2b 0%,#3d3d3b 35%,#8a8a86 60%,#bdbdb8 85%,#6d6d6a 100%)}
.hero-arrow{top:284px;width:42px;height:42px;border-radius:50%;background:rgba(40,40,40,.55);display:flex;align-items:center;justify-content:center}
.hero-arrow svg{width:14px;height:14px;stroke:var(--white);stroke-width:2.4;fill:none}

.dropdown{left:178px;top:153px;width:87px;height:72px;background:var(--red);padding:8px 0 0 12px}
.dropdown::before{content:"";position:absolute;left:25px;top:-5px;border:5px solid transparent;border-top:0;border-bottom-color:var(--red)}
.dropdown li{list-style:none;font-size:8.5px;color:var(--white);height:21.3px;display:flex;align-items:center;gap:6px}
.dropdown li::before{content:"";width:3px;height:3px;border-radius:50%;background:var(--white)}

.welcome-title{left:0;top:490px;width:811px;text-align:center;font-size:22px;font-weight:400;color:#444}
.welcome-title b,.section-title b{font-weight:700}
.welcome-text{left:100px;top:532px;width:611px;text-align:center;font-size:9px;line-height:17.5px;color:var(--muted)}
.btn{left:367px;top:594px;width:80px;height:27px;background:var(--red);color:var(--white);font-size:9px;display:flex;align-items:center;justify-content:center;border-bottom:2px solid #a81e14}

.divider{left:88px;width:635px;height:1px;background:var(--line)}

.section-title{left:0;width:811px;text-align:center;font-size:19.5px;font-weight:400;color:#444}
.section-title em{font-style:normal;font-weight:700;color:var(--red)}
.pager{left:703px;display:flex;gap:1px}
.pager svg{width:9px;height:11px;fill:none;stroke-width:2.4}

.project{top:716px;width:196px;text-align:center}
.project-photo{height:111px;border:3px solid #e8e8e8;background-clip:padding-box}
.project-name{margin-top:17px;font-size:10.5px;color:var(--red);font-weight:500}
.project-desc{margin-top:6px;font-size:8.5px;line-height:12.5px;color:var(--muted)}
.zoom{left:90px;top:38px;width:44px;height:44px;border-radius:50%;background:rgba(50,50,50,.75);color:var(--white);font-size:20px;display:flex;align-items:center;justify-content:center}

.post{top:989px;width:305px;height:106px;border:1px solid #dcdcdc;padding:15px 0 0 59px}
.avatar{left:12px;top:17px;width:36px;height:36px;border-radius:50%;background:linear-gradient(#c9c4bf,#8f8a86)}
.post-title{font-size:13px;font-weight:400;color:#333}
.post-text{margin-top:3px;font-size:8.5px;line-height:16px;color:var(--muted);width:232px}
.post-meta{margin-top:10px;display:flex;gap:10px;font-size:8px;color:#555}
.post-meta span{display:flex;align-items:center;gap:4px}
.post-meta svg{width:8px;height:8px;fill:none;stroke:#666;stroke-width:1.4}

.site-footer{left:0;top:1135px;width:811px;height:65px;background:var(--footer)}
.copyright{left:90px;top:33px;font-size:9px;color:#e6e6e6}
.to-top{left:706px;top:26px;width:18px;height:18px;border-radius:50%;background:var(--white);display:flex;align-items:center;justify-content:center}
.to-top svg{width:9px;height:9px;fill:none;stroke:var(--footer);stroke-width:2.6}
</style>
</head>
<body>

<div class="abs topbar">
  <div class="abs contact-item" style="left:88px"><svg viewBox="0 0 10 10"><rect x="0" y="0" width="10" height="10" rx="1.5"/></svg>02 40 11 302</div>
  <div class="abs contact-item" style="left:175px"><svg viewBox="0 0 10 10"><path d="M0 1.5h10v7H0z"/></svg>info@granviastone.com.au</div>
  <div class="abs contact-item" style="left:327px"><svg viewBox="0 0 10 10"><path d="M5 0a3.5 3.5 0 0 1 3.5 3.5C8.5 6 5 10 5 10S1.5 6 1.5 3.5A3.5 3.5 0 0 1 5 0z"/></svg>222 Building, Name City, Zipcode</div>
</div>

<header class="abs site-header">
  <div class="abs brand"><span class="brand-mark"></span>Granvia Stone</div>
  <div class="abs follow">Follow Us</div>
  <div class="abs socials">
    <span style="background:#1a67c0"></span>
    <span style="background:#2a8fe0"></span>
    <span style="background:#f0a030"></span>
    <span style="background:#cf3a2a"></span>
  </div>
</header>

<nav class="abs main-nav">
  <a class="abs nav-link" style="left:105px">Home</a>
  <a class="abs nav-link" style="left:177px">Collections</a>
  <a class="abs nav-link" style="left:277px">Projects</a>
  <a class="abs nav-link" style="left:354px">Installations</a>
  <a class="abs nav-link" style="left:446px">About us</a>
  <a class="abs nav-link" style="left:530px">Contact us</a>
</nav>

<div class="abs hero" role="img" aria-label="Slider photo of a lobby with a mosaic tiled floor, console table and staircase"></div>
<div class="abs hero-arrow" style="left:63px"><svg viewBox="0 0 14 14"><path d="M9 2 4 7l5 5"/></svg></div>
<div class="abs hero-arrow" style="left:711px"><svg viewBox="0 0 14 14"><path d="M5 2l5 5-5 5"/></svg></div>

<ul class="abs dropdown">
  <li>Granite</li>
  <li>Marble</li>
  <li>Sculpture</li>
</ul>

<h1 class="abs welcome-title">Welcome to Our Site <b>Mainpage</b></h1>
<p class="abs welcome-text">Lorem ipsum dolor sit amet, consectetur adipiscing elit, sed do eiusmod tempor incididunt ut labore et dolore magna aliqua. Ut enim ad minim veniam, quis nostrud exercitation ullamco laboris nisi ut aliquip ex ea commodo consequat. Duis aute irure dolor in reprehenderit in voluptate velit esse cillum dolore eu fugiat nulla pariatur epteur sint occaecat cupidatat non.</p>
<a class="abs btn">Read More</a>

<div class="abs divider" style="top:646px"></div>

<h2 class="abs section-title" style="top:675px">Recent <b>Projects</b></h2>
<div class="abs pager" style="top:683px">
  <svg viewBox="0 0 9 11" stroke="#444"><path d="M7 1 2 5.5 7 10"/></svg>
  <svg viewBox="0 0 9 11" stroke="#bbb"><path d="M2 1l5 4.5L2 10"/></svg>
</div>

<div class="abs project" style="left:88px">
  <div class="project-photo" role="img" aria-label="Bathroom with dark mosaic walls and white basins" style="background:linear-gradient(90deg,#a9aeb0,#4a4c50 55%,#2e3034)"></div>
  <div class="project-name">PROJECT NAME</div>
  <div class="project-desc">Duis aute irure dolor in reprehenderit<br>in voluptate velit esse cillu.</div>
</div>
<div class="abs project" style="left:307px">
  <div class="project-photo" role="img" aria-label="Gold mosaic wall behind lamps and a sideboard" style="position:relative;background:linear-gradient(135deg,#8c7a45,#b69a4c 45%,#6f6a55)">
    <div class="abs zoom">+</div>
  </div>
  <div class="project-name">PROJECT NAME</div>
  <div class="project-desc">Duis aute irure dolor in reprehenderit<br>in voluptate velit esse cillu.</div>
</div>
<div class="abs project" style="left:527px">
  <div class="project-photo" role="img" aria-label="Living room with a grey mosaic wall and armchairs" style="background:linear-gradient(180deg,#8d8c8e,#a9a6a3 60%,#d8d2c4)"></div>
  <div class="project-name">PROJECT NAME</div>
  <div class="project-desc">Duis aute irure dolor in reprehenderit<br>in voluptate velit esse cillu.</div>
</div>

<div class="abs divider" style="top:921px"></div>

<h2 class="abs section-title" style="top:948px">Our <em>Blog</em> Post</h2>
<div class="abs pager" style="top:954px">
  <svg viewBox="0 0 9 11" stroke="#444"><path d="M7 1 2 5.5 7 10"/></svg>
  <svg viewBox="0 0 9 11" stroke="#bbb"><path d="M2 1l5 4.5L2 10"/></svg>
</div>

<article class="abs post" style="left:89px">
  <div class="abs avatar" role="img" aria-label="Author portrait"></div>
  <h3 class="post-title">Duis aute irure dolor</h3>
  <p class="post-text">reprehenderit in voluptate velit esse cillum dolore eu fugiat nulla pariatur epteur sint occaec.</p>
  <div class="post-meta">
    <span><svg viewBox="0 0 8 8"><rect x=".7" y="1.2" width="6.6" height="6.1"/><path d="M.7 3h6.6"/></svg>March 14, 2014</span>
    <span><svg viewBox="0 0 8 8"><circle cx="4" cy="4" r="3.3"/><path d="M4 2v2h1.6"/></svg>8:28 PM</span>
  </div>
</article>
<article class="abs post" style="left:417px">
  <div class="abs avatar" role="img" aria-label="Author portrait"></div>
  <h3 class="post-title">Duis aute irure dolor</h3>
  <p class="post-text">reprehenderit in voluptate velit esse cillum dolore eu fugiat nulla pariatur epteur sint occaec.</p>
  <div class="post-meta">
    <span><svg viewBox="0 0 8 8"><rect x=".7" y="1.2" width="6.6" height="6.1"/><path d="M.7 3h6.6"/></svg>March 14, 2014</span>
    <span><svg viewBox="0 0 8 8"><circle cx="4" cy="4" r="3.3"/><path d="M4 2v2h1.6"/></svg>8:28 PM</span>
  </div>
</article>

<footer class="abs site-footer">
  <div class="abs copyright">Copyright ©2014. Yoursite. All Right Reserved</div>
  <div class="abs to-top"><svg viewBox="0 0 9 9"><path d="M1.5 6 4.5 3l3 3"/></svg></div>
</footer>

</body>
</html>
```